THE WELLNESS BARN WEBSITE for Physio, Fitness, health

An attractive website advertising a physiotherapyand fitness / gym business, not generic, colours are natural, greens, browns, beiges. No cheesy pictures. With the ability to sell a small,amount of goods online if i decide to. Simple to navigate. Text boxes that i can input the main information and change easily. Somewhere to put my timetable. Easy to find contact details. However many pages it needs, im not fussed.
Target Market(s)
People looking for rehabilitation or fitness classes
Industry/Entity Type
Physiotherapy, Fitness, Gym, Health
Coding
Coded - Design and coding required
Number of Pages Required
1 page
Font styles to use
Other font styles liked:
- Im not fusse,ld, not script
Requirements
Must have
- Will upload posts from my business insta page for reference about the feel. Earthy natural tones, I have a lot of timber, and rustic looking piece's, plants etc in my clinic
Nice to have
- Simple to navigate
Should not have
- Cheesy "yoga" or generic "people doing physio" pics

```html
<!DOCTYPE html>
<html lang="en">
<head>
<meta charset="utf-8">
<title>The Wellness Barn Kelpie Bay</title>
<link rel="stylesheet" href="https://fonts.googleapis.com/css2?family=Jost:wght@400;500;600&display=swap">
<style>
:root{
  --green:#2f4a1f;
  --green-mid:#3c5a2a;
  --green-panel:rgba(58,92,40,.9);
  --ink:#222;
  --muted:#555;
  --sage:#eef0ec;
  --sage-box:#e6e9e3;
  --star:#f2b01e;
  --white:#fff;
  --black:#000;
}
*{box-sizing:border-box;margin:0;padding:0}
html,body{width:1200px;height:4152px;overflow:hidden}
body{font-family:"Jost",sans-serif;color:var(--ink);background:var(--white);position:relative}
.abs{position:absolute}
.btn{position:absolute;background:var(--green);color:var(--white);border-radius:24px;font-size:14px;font-weight:500;text-transform:uppercase;display:flex;align-items:center;justify-content:center;letter-spacing:.2px}
.heading{position:absolute;left:0;width:100%;text-align:center;color:var(--green);font-weight:500;text-transform:uppercase}
.brand{font-weight:600;text-transform:uppercase;text-align:center;line-height:1.05;display:flex;align-items:center;gap:8px}
.brand-dot{width:14px;height:14px;border-radius:50%;background:currentColor;flex:none}

/* hero */
.hero{position:absolute;left:0;top:0;width:1200px;height:514px;background:linear-gradient(120deg,#3b3a2e 0%,#2d2c24 45%,#4a4632 75%,#2b2a22 100%)}
.hero .brand{position:absolute;left:104px;top:48px;color:var(--white);font-size:16px;width:110px}
.nav{position:absolute;top:52px;left:403px;display:flex;gap:0;font-size:13.5px;color:var(--white);font-weight:500;text-transform:uppercase}
.nav span{padding:8px 12px}
.nav .active{background:var(--green-mid)}
.hero .contact{left:980px;top:50px;width:108px;height:36px;font-size:13px}
.hero h1{position:absolute;top:143px;width:100%;text-align:center;color:var(--white);font-size:24px;font-weight:500;text-transform:uppercase}
.hero p{position:absolute;top:198px;left:240px;width:720px;text-align:center;color:#eee;font-size:15.5px;line-height:34.5px}
.hero .start{left:518px;top:335px;width:164px;height:40px;font-size:13px}

/* offer + services */
.sage{position:absolute;left:0;top:514px;width:1200px;height:958px;background:var(--sage)}
.offer{position:absolute;left:111px;top:441px;width:978px;height:311px;background:var(--white);border:1px solid #ddd}
.offer .brand{position:absolute;left:420px;top:30px;width:140px;color:var(--green);font-size:18px;justify-content:center}
.offer h2{top:146px;font-size:24px}
.offer p{position:absolute;top:192px;left:120px;width:738px;text-align:center;font-size:15.5px;line-height:34.5px}
.offer-btn{left:536px;top:730px;width:128px;height:43px}
.services-title{top:824px;font-size:29px}
.arrow{position:absolute;width:20px;height:20px}
.card{position:absolute;top:915px;width:305px;height:483px;overflow:hidden}
.card .photo{position:absolute;left:0;top:0;width:100%;height:265px}
.card .panel{position:absolute;left:0;top:265px;width:100%;bottom:0;background:var(--green-panel);padding:22px 28px;color:var(--white)}
.card h3{font-size:17px;font-weight:500;line-height:34px;text-transform:uppercase}
.card p{font-size:13.5px;line-height:29px;margin-top:8px}
.card .more{position:absolute;left:28px;bottom:24px;font-size:14px;font-weight:500;display:flex;gap:8px;align-items:center}
.card.full .photo{height:100%}
.card.full .panel{top:0;background:rgba(58,92,40,.88)}

/* stories */
.stories{position:absolute;left:111px;top:1549px;width:978px;height:476px;background:var(--sage-box)}
.stories h2{top:48px;font-size:30px}
.quote{position:absolute;top:118px;width:400px}
.stars{display:flex;gap:5px}
.quote p{font-size:15.5px;line-height:34.5px;margin-top:14px}
.person{display:flex;align-items:center;gap:24px;margin-top:20px}
.avatar{width:52px;height:52px;border-radius:50%;background:linear-gradient(#cbb19b,#8c6f5b);flex:none}
.person b{display:block;color:var(--green);font-weight:500;font-size:15px}
.person small{display:block;color:var(--muted);font-size:13.5px;margin-top:8px;text-transform:uppercase}
.stories .view{left:387px;top:381px;width:204px;height:41px}

/* products */
.products-title{top:2100px;font-size:30px}
.product-frame{position:absolute;left:121px;top:2195px;width:455px;height:330px;border:2px solid #666}
.product-img{position:absolute;left:111px;top:2203px;width:455px;height:325px;background:linear-gradient(135deg,#b89b7a 0%,#a2835f 40%,#5b4a3a 70%,#c06b45 100%)}
.product-info{position:absolute;left:641px;top:2192px;width:450px}
.product-info h3{color:var(--green);font-size:23px;font-weight:500;text-transform:uppercase}
.product-info p{font-size:14.5px;line-height:34.3px;margin-top:14px;color:#333}
.product-btn{left:641px;top:2473px;width:145px;height:42px}

/* team */
.team{position:absolute;left:0;top:2612px;width:1200px;height:748px;background:linear-gradient(90deg,#e9ebe6,#f2f3f0 50%,#e8eae5)}
.team h2{position:absolute;left:108px;top:50px;font-size:30px;color:var(--green);font-weight:500;text-transform:uppercase}
.team .divider{position:absolute;left:448px;top:56px;width:1px;height:110px;background:#bbb}
.team .kicker{position:absolute;left:539px;top:55px;font-size:15.5px;color:var(--muted);text-transform:uppercase}
.team .lead{position:absolute;left:539px;top:86px;font-size:14.5px;line-height:34.5px;width:300px}
.team .learn{left:944px;top:61px;width:144px;height:43px}
.member{position:absolute;top:210px;width:305px;height:490px;background:rgba(255,255,255,.35);border:1px solid #ddd}
.member .photo{width:100%;height:243px}
.socials{position:absolute;left:27px;top:222px;display:flex;gap:12px}
.socials span{width:42px;height:42px;border-radius:50%;background:var(--green);border:2px solid var(--white);display:block}
.member .info{padding:48px 23px 0}
.member h3{color:var(--green);font-size:20px;font-weight:500;text-transform:uppercase}
.member h4{font-size:14.5px;font-weight:500;text-transform:uppercase;margin-top:18px}
.member p{font-size:14.5px;line-height:34px;color:var(--muted);margin-top:12px}

/* contact */
.contact-col{position:absolute;top:3445px;width:290px;text-align:center}
.icon{width:56px;height:56px;border-radius:50%;background:var(--green);margin:0 auto;display:flex;align-items:center;justify-content:center}
.contact-col h3{color:var(--green);font-size:20px;font-weight:500;margin-top:40px;text-transform:uppercase}
.contact-col p{font-size:14.5px;line-height:33.8px;color:var(--muted);margin-top:12px}
.contact-col p span{color:var(--ink)}

/* footer */
.footer{position:absolute;left:0;top:3814px;width:1200px;height:338px;background:var(--black);color:var(--white)}
.footer .brand{position:absolute;left:520px;top:58px;width:160px;font-size:24px;justify-content:center}
.footer-nav{position:absolute;top:205px;width:100%;display:flex;justify-content:center;gap:24px;font-size:14px;text-transform:uppercase}
.copy{position:absolute;top:255px;width:100%;text-align:center;font-size:13.5px;text-transform:uppercase}
</style>
</head>
<body>

<header class="hero" role="img" aria-label="Dim studio interior with a person seated on a mat among plants and armchairs">
  <div class="brand"><span class="brand-dot"></span>The Wellness Barn</div>
  <nav class="nav">
    <span class="active">Home</span><span>What do we</span><span>Success stories</span><span>Meet our team</span><span>FAQs</span>
  </nav>
  <div class="btn contact">Contact us</div>
  <h1>Welcome to The Wellness Barn Kelpie Bay</h1>
  <p>Discover a healthier you with our Physiotherapist led programs. At The Wellness Barn Kelpie Bay, we focus on safe and effective movement to enhance your quality of life. Join us for a comprehensive approach to wellbeing.</p>
  <div class="btn start">Get started now</div>
</header>

<section class="sage"></section>
<section class="offer">
  <div class="brand"><span class="brand-dot"></span>The Wellness Barn</div>
  <h2 class="heading">What do we have to offer?</h2>
  <p>The Wellness Barn Kelpie Bay is dedicated to empowering individuals to achieve their health and wellbeing goals through safe and effective movement.</p>
</section>
<div class="btn offer-btn">Read more</div>

<h2 class="heading services-title">Wellness Barn Services</h2>
<svg class="arrow" style="left:40px;top:1147px" viewBox="0 0 20 20"><path d="M13 3 6 10l7 7" fill="none" stroke="#111" stroke-width="2.2"/></svg>
<svg class="arrow" style="left:1126px;top:1147px" viewBox="0 0 20 20"><path d="M7 3l7 7-7 7" fill="none" stroke="#111" stroke-width="2.2"/></svg>

<article class="card" style="left:119px">
  <div class="photo" role="img" aria-label="Physiotherapist guiding a client through a side stretch by a window" style="background:linear-gradient(135deg,#e6e6e2,#b9bcb4 55%,#6f7d6a)"></div>
  <div class="panel">
    <h3>Physiotherapy classes for everyone</h3>
    <p>Our classes are tailored for all ages, focusing on safe movement</p>
    <div class="more">Learn more <svg width="12" height="12" viewBox="0 0 12 12"><path d="M2 10 10 2M4 2h6v6" fill="none" stroke="#fff" stroke-width="1.5"/></svg></div>
  </div>
</article>
<article class="card full" style="left:447px">
  <div class="photo" role="img" aria-label="Person seated on the floor in a bright room" style="background:linear-gradient(160deg,#c9c8b8,#8e9a80)"></div>
  <div class="panel">
    <h3>Holistic wellness programs</h3>
    <p>Our programs integrate physical activity with nutritional guidance to support sustainable health improvements.</p>
    <div class="more">Learn more <svg width="12" height="12" viewBox="0 0 12 12"><path d="M2 10 10 2M4 2h6v6" fill="none" stroke="#fff" stroke-width="1.5"/></svg></div>
  </div>
</article>
<article class="card" style="left:775px">
  <div class="photo" role="img" aria-label="Person holding a standing lunge pose against a pale wall" style="background:linear-gradient(180deg,#e4ecee,#cfdbe0)"></div>
  <div class="panel">
    <h3>Mindfulness and yoga sessions</h3>
    <p>Join our yoga sessions to improve mental clarity and physical</p>
    <div class="more">Learn more <svg width="12" height="12" viewBox="0 0 12 12"><path d="M2 10 10 2M4 2h6v6" fill="none" stroke="#fff" stroke-width="1.5"/></svg></div>
  </div>
</article>

<section class="stories">
  <h2 class="heading">Client success stories</h2>
  <div class="quote" style="left:66px">
    <div class="stars">
      <svg width="18" height="18" viewBox="0 0 20 20"><path d="M10 1l2.7 6 6.3.6-4.8 4.3 1.4 6.4L10 15l-5.6 3.3 1.4-6.4L1 7.6 7.3 7z" fill="#f2b01e"/></svg>
      <svg width="18" height="18" viewBox="0 0 20 20"><path d="M10 1l2.7 6 6.3.6-4.8 4.3 1.4 6.4L10 15l-5.6 3.3 1.4-6.4L1 7.6 7.3 7z" fill="#f2b01e"/></svg>
      <svg width="18" height="18" viewBox="0 0 20 20"><path d="M10 1l2.7 6 6.3.6-4.8 4.3 1.4 6.4L10 15l-5.6 3.3 1.4-6.4L1 7.6 7.3 7z" fill="#f2b01e"/></svg>
      <svg width="18" height="18" viewBox="0 0 20 20"><path d="M10 1l2.7 6 6.3.6-4.8 4.3 1.4 6.4L10 15l-5.6 3.3 1.4-6.4L1 7.6 7.3 7z" fill="#f2b01e"/></svg>
      <svg width="18" height="18" viewBox="0 0 20 20"><path d="M10 1l2.7 6 6.3.6-4.8 4.3 1.4 6.4L10 15l-5.6 3.3 1.4-6.4L1 7.6 7.3 7z" fill="#f2b01e"/></svg>
    </div>
    <p>The Wellness Barn has completely changed my approach to fitness. Their programs are tailored and effective!</p>
    <div class="person"><div class="avatar" role="img" aria-label="Client portrait"></div><div><b>TESSA MORLAND</b><small>Fitness enthusiast</small></div></div>
  </div>
  <div class="quote" style="left:555px">
    <div class="stars">
      <svg width="18" height="18" viewBox="0 0 20 20"><path d="M10 1l2.7 6 6.3.6-4.8 4.3 1.4 6.4L10 15l-5.6 3.3 1.4-6.4L1 7.6 7.3 7z" fill="#f2b01e"/></svg>
      <svg width="18" height="18" viewBox="0 0 20 20"><path d="M10 1l2.7 6 6.3.6-4.8 4.3 1.4 6.4L10 15l-5.6 3.3 1.4-6.4L1 7.6 7.3 7z" fill="#f2b01e"/></svg>
      <svg width="18" height="18" viewBox="0 0 20 20"><path d="M10 1l2.7 6 6.3.6-4.8 4.3 1.4 6.4L10 15l-5.6 3.3 1.4-6.4L1 7.6 7.3 7z" fill="#f2b01e"/></svg>
      <svg width="18" height="18" viewBox="0 0 20 20"><path d="M10 1l2.7 6 6.3.6-4.8 4.3 1.4 6.4L10 15l-5.6 3.3 1.4-6.4L1 7.6 7.3 7z" fill="#f2b01e"/></svg>
      <svg width="18" height="18" viewBox="0 0 20 20"><path d="M10 1l2.7 6 6.3.6-4.8 4.3 1.4 6.4L10 15l-5.6 3.3 1.4-6.4L1 7.6 7.3 7z" fill="#f2b01e"/></svg>
    </div>
    <p>I never thought I could regain my mobility. The physiotherapy classes here are a game changer!</p>
    <div class="person"><div class="avatar" role="img" aria-label="Client portrait" style="background:linear-gradient(#d9c2aa,#9a7f66)"></div><div><b>GRAHAM ELLERY</b><small>Retired veteran</small></div></div>
  </div>
  <div class="btn view">View more stories</div>
</section>

<h2 class="heading products-title">Our products</h2>
<svg class="arrow" style="left:40px;top:2347px" viewBox="0 0 20 20"><path d="M13 3 6 10l7 7" fill="none" stroke="#111" stroke-width="2.2"/></svg>
<svg class="arrow" style="left:1126px;top:2347px" viewBox="0 0 20 20"><path d="M7 3l7 7-7 7" fill="none" stroke="#111" stroke-width="2.2"/></svg>
<div class="product-frame"></div>
<div class="product-img" role="img" aria-label="Kraft gift boxes and a rust-coloured heat pack on a timber table"></div>
<div class="product-info">
  <h3>Grain Pillow Co</h3>
  <p>Lorem ipsum dolor sit amet, consectetur adipiscing elit, sed do eiusmod tempor incididunt ut labore et dolore magna aliqua. Ut enim ad minim veniam, quis nostrud exercitation ullamco laboris nisi ut aliquip ex ea commodo consequat. Duis aute irure dolor in reprehenderit in voluptate velit esse cillum dolore eu fugiat nulla pariatur.</p>
</div>
<div class="btn product-btn">Learn more</div>

<section class="team" role="region" aria-label="Meet our team">
  <h2>Meet our team</h2>
  <div class="divider"></div>
  <div class="kicker">Get to know us</div>
  <div class="lead">Discover the dedicated professionals committed to your health.</div>
  <div class="btn learn">Learn more</div>

  <article class="member" style="left:111px">
    <div class="photo" role="img" aria-label="Portrait of the lead physiotherapist in a bright clinic" style="background:linear-gradient(160deg,#f1ede8,#d8cfc6)"></div>
    <div class="socials"><span></span><span></span></div>
    <div class="info"><h3>Dr. Helen Marsh</h3><h4>Lead physiotherapist</h4><p>Dr. Helen specializes in sports rehabilitation and has over 10 years of experience...</p></div>
  </article>
  <article class="member" style="left:446px">
    <div class="photo" role="img" aria-label="Portrait of the wellness coach in a library" style="background:linear-gradient(160deg,#6b5a45,#a89a86 60%,#3a3f45)"></div>
    <div class="socials"><span></span><span></span></div>
    <div class="info"><h3>Owen Prescott</h3><h4>Wellness coach</h4><p>Owen focuses on holistic health and wellness, guiding clients through lifestyle changes...</p></div>
  </article>
  <article class="member" style="left:782px">
    <div class="photo" role="img" aria-label="Portrait of the physiotherapy assistant in a treatment room" style="background:linear-gradient(160deg,#e9e2d8,#c9b8a4 60%,#4f6f8c)"></div>
    <div class="socials"><span></span><span></span></div>
    <div class="info"><h3>Lucy Tran</h3><h4>Physiotherapy assistant</h4><p>Lucy assists in physiotherapy sessions and is passionate about helping clients achieve...</p></div>
  </article>
</section>

<div class="contact-col" style="left:114px">
  <div class="icon"><svg width="22" height="16" viewBox="0 0 22 16"><rect x="1" y="1" width="20" height="14" rx="1.5" fill="#fff"/><path d="M1 2l10 7 10-7" fill="none" stroke="#2f4a1f" stroke-width="1.6"/></svg></div>
  <h3>Email us</h3>
  <p>For inquiries or more information, feel free to reach out via email at <span>hello@wellnessbarnkelpiebay.com</span>. We are here to assist you with any questions you may have.</p>
</div>
<div class="contact-col" style="left:464px">
  <div class="icon"><svg width="20" height="20" viewBox="0 0 24 24"><path d="M6.6 10.8a15 15 0 0 0 6.6 6.6l2.2-2.2a1 1 0 0 1 1-.25 11.4 11.4 0 0 0 3.6.57 1 1 0 0 1 1 1V20a1 1 0 0 1-1 1A17 17 0 0 1 3 4a1 1 0 0 1 1-1h3.5a1 1 0 0 1 1 1c0 1.25.2 2.45.57 3.57a1 1 0 0 1-.25 1z" fill="#fff"/></svg></div>
  <h3>Call us</h3>
  <p>You can contact us directly at +61 7 4000 1287. Our team is available to take your calls and provide support during business hours.</p>
</div>
<div class="contact-col" style="left:807px">
  <div class="icon"><svg width="20" height="24" viewBox="0 0 20 24"><path d="M10 1a8 8 0 0 0-8 8c0 6 8 14 8 14s8-8 8-14a8 8 0 0 0-8-8z" fill="none" stroke="#fff" stroke-width="2"/><circle cx="10" cy="9" r="3" fill="#fff"/></svg></div>
  <h3>Visit us</h3>
  <p>We are located at 48 Timber Lane, Kelpie Bay, Australia, 4699. Come visit us to learn more about our programs and how we can help you achieve your health goals.</p>
</div>

<footer class="footer">
  <div class="brand"><span class="brand-dot"></span>The Wellness Barn</div>
  <nav class="footer-nav"><span>Home</span><span>|</span><span>About us</span><span>|</span><span>Programs</span><span>|</span><span>Testimonials</span><span>|</span><span>Contact us</span></nav>
  <div class="copy">© 2025 The Wellness Barn Kelpie Bay. All rights reserved &nbsp;|&nbsp; Terms and conditions &nbsp;|&nbsp; Privacy policy</div>
</footer>

</body>
</html>
```